Lantern Petals Website v.1 - attract floral shop franchisees

I need a simple information website for my new business. We are a franchisor of flower shops. The overall purpose of the website is to promote the company and the service, especially to potential franchisees and retailers. Only about 4 pages are required including homepage, About, For Supermarkets, For Franchisees, and Contact. No special functions are required except the site will have two separate inquiry forms that must be filled out online and submitted via automated email. Similarly, an email form should be linked from the Contact page. I have a logo and business cards designed by ArtMingle, and I would like the site to have a consistent color scheme and style. The key to design will be to express the joy and love associated with flowers and floral bouquets.
IMPORTANT - I will be exporting the website design to Wordpress CMS in a site hosted by HostNimbus. For smooth integration into WordPress hosted by HostNimbus, the designer should build the site using a WordPress-friendly format. Ideally, they should use HTML, CSS, and PHP. Creating a custom theme or using a page builder that exports to WordPress-compatible files is best. This ensures the site can be easily imported and managed within WordPress.

Target Market(s)

Potential franchisees (existing florists or creative types who might like to own a floral business) and supermarkets who might want us to run their floral department

Industry/Entity Type

Floral retailing

Requirements
Must have
• A brand theme that is beautiful, consistent throughout and builds on the logo design
Nice to have
• Show gender and ethnic diversity in customers and florists. Pictures of happy florists (for franchisees) and pictures of amazing floral department displays (for supermarkets)

```html
<!DOCTYPE html>
<html lang="en">
<head>
<meta charset="utf-8">
<title>Lantern Petals – Home</title>
<link href="https://fonts.googleapis.com/css2?family=Poppins:wght@500;600&family=Quicksand:wght@400;500;600&family=Great+Vibes&display=swap" rel="stylesheet">
<style>
:root{
  --green:#0c8a38;
  --orange:#f29a05;
  --ink:#333;
  --muted:#4a4a4a;
  --grey:#efefef;
  --cream:#fdf5e6;
  --white:#fff;
  --dark:#2b2f26;
}
*{margin:0;padding:0;box-sizing:border-box}
html,body{width:1200px;height:3443px;overflow:hidden;background:var(--white);font-family:"Quicksand",sans-serif;color:var(--ink)}
.page{position:relative;width:1200px;height:3443px}
.abs{position:absolute}
.brand{font-family:"Quicksand",sans-serif;font-weight:600;color:var(--orange);display:flex;align-items:center;gap:10px}
.brand-dot{width:26px;height:26px;border-radius:50%;background:var(--orange)}
.header-brand{left:140px;top:30px;font-size:30px}
.contact-chip{display:flex;align-items:center;gap:12px;font-size:15px;font-weight:500;color:#222}
.chip-icon{width:36px;height:36px;border-radius:50%;background:var(--orange);display:flex;align-items:center;justify-content:center}
.nav{left:0;top:98px;width:1200px;height:43px;background:var(--green);display:flex;align-items:center;padding:0 140px;justify-content:space-between;color:var(--white);font-size:13px;font-weight:500}
.nav .active{font-weight:600;position:relative}
.nav .active:after{content:"";position:absolute;left:50%;bottom:-8px;width:4px;height:4px;margin-left:-2px;border-radius:50%;background:var(--orange)}
.hero-photo{left:0;top:141px;width:1200px;height:560px;background:linear-gradient(160deg,#3a3a30 0%,#5b4a45 40%,#6b4752 65%,#3f3a48 100%)}
.hero-shade{left:0;top:141px;width:1200px;height:560px;background:rgba(20,20,15,.45)}
.hero-title{left:140px;top:268px;font-family:"Poppins",sans-serif;font-weight:600;font-size:37px;line-height:53px;color:var(--white)}
.btn{left:140px;top:450px;width:142px;height:41px;border-radius:21px;background:var(--orange);color:var(--white);font-size:14px;font-weight:500;display:flex;align-items:center;justify-content:center}
.hero-arch{left:625px;top:290px;width:433px;height:400px;border-radius:217px 217px 0 0;border:3px solid var(--orange);padding:6px}
.hero-arch div{width:100%;height:100%;border-radius:210px 210px 0 0;background:linear-gradient(180deg,#f0a20f,#e59208)}
.hero-person{left:705px;top:160px;width:290px;height:520px;border-radius:140px 140px 20px 20px;background:linear-gradient(180deg,#8a6a55 0%,#6f94b5 45%,#4d5a6a 100%);opacity:.9}
.wave{left:0;top:590px}
.photo{background:linear-gradient(160deg,#c9b08a,#9c5a3a 45%,#6d7a3f)}
.about-a{left:144px;top:840px;width:244px;height:315px;border-radius:0 0 0 140px;border-top-right-radius:0;background:linear-gradient(150deg,#a7b7a0,#e6c84a 60%,#8a8f9a)}
.about-a{border-radius:120px 0 0 120px / 140px 0 0 140px}
.about-a{border-radius:0 120px 0 140px}
.about-b{left:409px;top:790px;width:176px;height:222px;border-radius:0 0 120px 0;background:linear-gradient(160deg,#d9c7a0,#e38a2a 50%,#4e6a35)}
.about-c{left:409px;top:1033px;width:176px;height:222px;border-radius:120px 0 0 0;background:linear-gradient(160deg,#7a4a35,#d24a7a 50%,#5a7a3a)}
.script{font-family:"Great Vibes",cursive;font-size:52px;color:#111;line-height:1}
.script span{color:var(--orange)}
.divider{display:flex;align-items:center;gap:8px}
.divider i{display:block;width:42px;height:2px;background:var(--green)}
.divider b{display:block;width:12px;height:12px;border-radius:50%;background:var(--green)}
.copy{font-size:12px;line-height:23px;color:var(--muted)}
.copy p+p{margin-top:6px}
.deco{background:rgba(150,165,175,.18);border-radius:12px}
.grey-band{left:0;top:1340px;width:1200px;height:460px;background:var(--grey)}
.arch-card{left:668px;top:1412px;width:383px;height:488px;background:var(--white);border-radius:192px 192px 0 0;padding:14px 10px 12px;box-shadow:0 4px 14px rgba(0,0,0,.06)}
.arch-card div{width:100%;height:100%;border-radius:0;background:linear-gradient(160deg,#4a3a30,#9a6a5a 45%,#7a8aa0 70%,#5a3a2a)}
.arrow{width:45px;height:45px;border-radius:50%;border:2px solid var(--green);display:flex;align-items:center;justify-content:center}
.arrow.fill{background:var(--green)}
.dark-band{left:0;top:2172px;width:1200px;height:400px;background:linear-gradient(180deg,#2a3326,#1f2a1f 60%,#2b2223)}
.dark-shade{left:0;top:2172px;width:1200px;height:400px;background:rgba(0,0,0,.25)}
.gal{top:1970px;width:215px;height:300px;border:3px solid var(--white);background-clip:padding-box}
.partner{left:0;top:2365px;width:1200px;text-align:center;color:var(--white);font-size:15px;font-weight:600;letter-spacing:4px;display:flex;justify-content:center;align-items:center;gap:10px}
.partner-dot{width:14px;height:14px;border-radius:50%;background:rgba(255,255,255,.7)}
.partner-copy{left:160px;top:2440px;width:880px;text-align:center;color:var(--white);font-size:12.5px;line-height:23px}
.t-card{left:217px;top:2793px;width:766px;height:212px;border-radius:22px;background:var(--cream)}
.avatar{left:564px;top:2758px;width:72px;height:72px;border-radius:50%;border:3px solid var(--white);background:linear-gradient(180deg,#c9a58a,#7aa9cc)}
.t-name{left:0;top:2855px;width:1200px;text-align:center;font-family:"Great Vibes",cursive;font-size:24px;color:#111}
.t-name span{color:var(--orange)}
.t-text{left:350px;top:2897px;width:500px;text-align:center;font-size:12.5px;line-height:23px;color:#333}
.stars{left:0;top:2955px;width:1200px;text-align:center;color:var(--orange);font-size:16px;letter-spacing:3px}
.footer{left:0;top:3087px;width:1200px;height:356px;background:var(--green);color:var(--white)}
.f-title{font-family:"Great Vibes",cursive;font-size:26px;color:var(--white)}
.f-divider i,.f-divider b{background:var(--white)}
.f-links{list-style:none;font-size:12.5px;line-height:33px}
.social{display:flex;gap:8px}
.social span{width:28px;height:28px;border-radius:50%;border:1.5px solid var(--white)}
.f-row{display:flex;align-items:center;gap:14px;font-size:12.5px;line-height:18px}
.f-row .chip-icon{width:38px;height:38px;flex:none;border:2px solid rgba(255,255,255,.5)}
.f-rule{left:140px;top:3402px;width:920px;height:1px;background:rgba(255,255,255,.25)}
.copyright{left:0;top:3418px;width:1200px;text-align:center;font-size:12px}
</style>
</head>
<body>
<div class="page">

  <!-- Header -->
  <div class="abs brand header-brand"><span class="brand-dot"></span>Lantern Petals</div>
  <div class="abs contact-chip" style="left:672px;top:31px">
    <span class="chip-icon"><svg width="16" height="16" viewBox="0 0 24 24"><path fill="#fff" d="M6.6 10.8a15 15 0 0 0 6.6 6.6l2.2-2.2c.3-.3.7-.4 1-.2 1.1.4 2.3.6 3.6.6.6 0 1 .4 1 1V20c0 .6-.4 1-1 1A17 17 0 0 1 3 4c0-.6.4-1 1-1h3.5c.6 0 1 .4 1 1 0 1.3.2 2.5.6 3.6.1.3 0 .7-.2 1z"/></svg></span>123-456-7890
  </div>
  <div class="abs contact-chip" style="left:846px;top:31px">
    <span class="chip-icon"><svg width="16" height="12" viewBox="0 0 20 14"><rect x="1" y="1" width="18" height="12" rx="1.5" fill="none" stroke="#fff" stroke-width="1.8"/><path d="M1.5 2 10 8l8.5-6" fill="none" stroke="#fff" stroke-width="1.8"/></svg></span>info@lanternpetals.com
  </div>

  <nav class="abs nav">
    <span class="active">Home</span><span>|</span><span>About Us</span><span>|</span><span>For Supermarkets</span><span>|</span><span>For Franchisees</span><span>|</span><span>Contact Us</span>
  </nav>

  <!-- Hero -->
  <div class="abs hero-photo" role="img" aria-label="Flower shop buckets full of roses and mixed blooms"></div>
  <div class="abs hero-shade"></div>
  <h1 class="abs hero-title">Freshest Flowers<br>Artisan Designs<br>Franchise Opportunities</h1>
  <div class="abs btn">Contact Us</div>
  <div class="abs hero-arch"><div></div></div>
  <div class="abs hero-person" role="img" aria-label="Smiling florist in an apron holding a large colourful bouquet"></div>
  <svg class="abs wave" width="1200" height="120" viewBox="0 0 1200 120">
    <path d="M0 90 C150 10 330 25 560 80 C760 125 1000 110 1200 10 L1200 120 L0 120Z" fill="#0c8a38"/>
    <path d="M0 110 C160 40 340 50 560 95 C760 135 1000 125 1200 28 L1200 120 L0 120Z" fill="#fff"/>
  </svg>

  <!-- About -->
  <div class="abs about-a" role="img" aria-label="Florist standing behind buckets of yellow and white flowers"></div>
  <div class="abs about-b" role="img" aria-label="Tall arrangement of orange protea and tropical flowers"></div>
  <div class="abs about-c" role="img" aria-label="Pink and red bouquets in glass vases"></div>
  <h2 class="abs script" style="left:650px;top:812px">About <span>Us</span></h2>
  <div class="abs divider" style="left:652px;top:872px"><i></i><b></b><i></i></div>
  <div class="abs copy" style="left:650px;top:910px;width:405px">
    <p>Fresh flowers convey beauty and love, and in our view should become something every person regularly enjoys.&nbsp; Lantern Petals is an entrepreneurial company created to make top quality fresh flowers and professionally-designed bouquets accessible to every consumer at affordable prices.</p>
    <p>Professional florists typically sell the finest quality stems, design the most beautiful bouquets and provide the finest customer service, but their costs – of floral products, retail spaces, labor and marketing – force them to pass high prices along to customers. Supermarket flower departments benefit from high customer footfall, economies of scale and low pricing, but their quality of stems and bouquets is typically poor, staffing is limited, and staff turnover is high which can result in inefficiency, wastage, poorly merchandised selections and limited service.</p>
  </div>
  <div class="abs deco" style="left:988px;top:1045px;width:212px;height:282px" role="img" aria-label="Line drawing of a lily stem"></div>

  <!-- Network -->
  <div class="abs grey-band"></div>
  <div class="abs copy" style="left:140px;top:1452px;width:445px">
    <p>Lantern Petals brings the best of professional florists and supermarkets together for the benefit of consumers.&nbsp; It supports a national network of owner-operator franchisees, who in many cases are multi-site professional florists, with comprehensive services to enhance franchise profitability.&nbsp; Lantern Petals works with some of the country's largest and most progressive supermarkets to provide franchisee ownership and operation of their strategically important floral departments.</p>
    <p>Supermarkets find that Lantern Petals is able to improve their financial outcomes, provide attentive customer service and satisfaction, and lift the quality of the entire store environment.</p>
  </div>
  <div class="abs deco" style="left:18px;top:1648px;width:102px;height:136px" role="img" aria-label="Line drawing of blossoms"></div>
  <div class="abs arch-card"><div role="img" aria-label="Florist trimming stems at a workbench"></div></div>
  <div class="abs arrow" style="left:542px;top:1822px"><svg width="10" height="12" viewBox="0 0 10 12"><path d="M7 1 2 6l5 5" fill="none" stroke="#222" stroke-width="2"/></svg></div>
  <div class="abs arrow fill" style="left:602px;top:1822px"><svg width="10" height="12" viewBox="0 0 10 12"><path d="M3 1l5 5-5 5" fill="none" stroke="#fff" stroke-width="2"/></svg></div>

  <!-- Partner band -->
  <div class="abs dark-band" role="img" aria-label="Field of red gerbera flowers"></div>
  <div class="abs dark-shade"></div>
  <div class="abs gal photo" style="left:140px;border-radius:0 0 100px 0;background:linear-gradient(160deg,#d8d8d0,#b0305a 45%,#3f6a30)" role="img" aria-label="Crate of roses and peonies"></div>
  <div class="abs gal photo" style="left:375px;top:2000px;border-radius:0 100px 0 0;background:linear-gradient(160deg,#c9b8a8,#e58aa0 45%,#b82a2a 75%,#8aa03a)" role="img" aria-label="Florist arranging a pink bouquet"></div>
  <div class="abs gal photo" style="left:610px;border-radius:0 0 100px 0;background:linear-gradient(160deg,#2f4a35,#d8a0a8 50%,#5a6a3a)" role="img" aria-label="Flower shop storefront with displays"></div>
  <div class="abs gal photo" style="left:845px;top:2000px;border-radius:0 100px 0 0;background:linear-gradient(160deg,#eeeae4,#b83030 55%,#f0eeea)" role="img" aria-label="Smiling florist with red and white flowers"></div>
  <div class="abs partner"><span class="partner-dot"></span>NORTHWAVE GROUP</div>
  <p class="abs partner-copy">Lantern Petals operates in partnership with Northwave Group, the leading franchisor of sushi stations and pre-packaged fruit &amp; vegetable departments to supermarkets across the United States and United Kingdom.&nbsp; Lantern Petals' combination of floral and supermarket franchising expertise guarantees that consumers, franchisees and supermarket partners each receive exceptional service and value.</p>

  <!-- Testimonials -->
  <h2 class="abs script" style="left:0;width:1200px;text-align:center;top:2655px">What Our Customers <span>Say</span></h2>
  <div class="abs divider" style="left:538px;top:2716px"><i></i><b></b><i></i></div>
  <div class="abs t-card"></div>
  <div class="abs deco" style="left:240px;top:2845px;width:90px;height:130px" role="img" aria-label="Line drawing of a flowering sprig"></div>
  <div class="abs deco" style="left:862px;top:2840px;width:105px;height:150px" role="img" aria-label="Line drawing of a leafy branch"></div>
  <div class="abs avatar" role="img" aria-label="Customer portrait"></div>
  <div class="abs t-name">Mira <span>Hollins</span></div>
  <p class="abs t-text">Lorem ipsum dolor sit amet, consectetur adipiscing elit, sed do eiusmod tempor incididunt ut labore et dolore magna aliqua.</p>
  <div class="abs stars">★★★★★</div>
  <div class="abs arrow" style="left:157px;top:2881px;width:35px;height:35px"><svg width="8" height="10" viewBox="0 0 10 12"><path d="M7 1 2 6l5 5" fill="none" stroke="#222" stroke-width="2"/></svg></div>
  <div class="abs arrow fill" style="left:1008px;top:2881px;width:35px;height:35px"><svg width="8" height="10" viewBox="0 0 10 12"><path d="M3 1l5 5-5 5" fill="none" stroke="#fff" stroke-width="2"/></svg></div>

  <!-- Footer -->
  <footer class="abs footer">
    <div class="abs f-title" style="left:140px;top:53px">Quick Links</div>
    <div class="abs divider f-divider" style="left:141px;top:95px"><i style="width:20px"></i><b style="width:8px;height:8px"></b><i style="width:20px"></i></div>
    <ul class="abs f-links" style="left:141px;top:110px">
      <li>Home</li><li>About Us</li><li>For Supermarkets</li><li>For Franchisees</li><li>Contact Us</li>
    </ul>
    <div class="abs brand" style="left:420px;top:132px;font-size:40px"><span class="brand-dot" style="width:34px;height:34px"></span>Lantern Petals</div>
    <div class="abs social" style="left:482px;top:228px"><span></span><span></span><span></span><span></span></div>
    <div class="abs f-title" style="left:853px;top:53px">Contact Details</div>
    <div class="abs divider f-divider" style="left:854px;top:95px"><i style="width:20px"></i><b style="width:8px;height:8px"></b><i style="width:20px"></i></div>
    <div class="abs f-row" style="left:853px;top:122px"><span class="chip-icon"><svg width="12" height="16" viewBox="0 0 12 16"><path d="M6 0a6 6 0 0 1 6 6c0 4.5-6 10-6 10S0 10.5 0 6a6 6 0 0 1 6-6z" fill="#fff"/><circle cx="6" cy="6" r="2.2" fill="#f29a05"/></svg></span>123, Building Name, Street<br>City, State XY 123456</div>
    <div class="abs f-row" style="left:853px;top:185px"><span class="chip-icon"><svg width="15" height="15" viewBox="0 0 24 24"><path fill="#fff" d="M6.6 10.8a15 15 0 0 0 6.6 6.6l2.2-2.2c.3-.3.7-.4 1-.2 1.1.4 2.3.6 3.6.6.6 0 1 .4 1 1V20c0 .6-.4 1-1 1A17 17 0 0 1 3 4c0-.6.4-1 1-1h3.5c.6 0 1 .4 1 1 0 1.3.2 2.5.6 3.6.1.3 0 .7-.2 1z"/></svg></span>123-456-7890</div>
    <div class="abs f-row" style="left:853px;top:236px"><span class="chip-icon"><svg width="15" height="11" viewBox="0 0 20 14"><rect x="1" y="1" width="18" height="12" rx="1.5" fill="none" stroke="#fff" stroke-width="1.8"/><path d="M1.5 2 10 8l8.5-6" fill="none" stroke="#fff" stroke-width="1.8"/></svg></span>info@lanternpetals.com</div>
  </footer>
  <div class="abs f-rule"></div>
  <div class="abs copyright" style="color:#fff">©2024 Lantern Petals. All Rights Reserved.</div>
</div>
</body>
</html>
```